Business Card Design Project

I have a two letter domain name zu.com.au (lower case font please). I want a business card, cum logo that is die cut (around the zu segment at least) that fits standard business card size.
zu is all about what 'I am' - a journalist, blogger, analyst, commentator. My mantra is "I think therefore zu'.
The reverse of the card only needs my name Olin Verka, email olin@zu.com.au and mobile +61 437 185 923
Mainly people that will use my professional writing services and suppliers that will provide product for review
Business
- One side is zu.com.au (hint - the .com.au can be vertical or horizontal to fit - the zu should be as large as possible).
The other requires large size font name, email and phone details (so no one needs glasses to read it).
The die cut can be just to highlight the zu segment - need not be around the whole card.
Font used in the past was Belwe (old style - very much like the i used in the information symbol).
Colours - no preference - prefer two colour to process colour but can also be an outline font instead of solid colour.

```html
<!DOCTYPE html>
<html lang="en">
<head>
<meta charset="utf-8">
<title>zu.com.au business card</title>
<link rel="stylesheet" href="https://fonts.googleapis.com/css2?family=Jost:wght@500;700;800&display=swap">
<style>
  :root {
    --backdrop: #d6d6d3;
    --navy: #2a2a7e;
    --green: #00d95a;
  }
  * { margin: 0; padding: 0; box-sizing: border-box; }
  html, body {
    width: 1200px;
    height: 1000px;
    overflow: hidden;
    background: var(--backdrop);
  }
  .canvas {
    position: relative;
    width: 1200px;
    height: 1000px;
  }
  .card {
    position: absolute;
    width: 470px;
    height: 260px;
    overflow: hidden;
    font-family: "Jost", "Futura", sans-serif;
  }
  .card-front {
    left: 120px;
    top: 330px;
    background: var(--navy);
  }
  .card-back {
    left: 610px;
    top: 410px;
    background: var(--green);
  }
  .cut-mark {
    position: absolute;
    font-weight: 800;
    font-size: 230px;
    line-height: 1;
    letter-spacing: -6px;
    color: var(--backdrop);
  }
  .card-front .cut-mark {
    left: 100px;
    top: -14px;
  }
  .card-back .cut-mark {
    left: 120px;
    top: -16px;
    transform: scaleX(-1);
  }
  .domain-suffix {
    position: absolute;
    left: 188px;
    top: 200px;
    font-weight: 500;
    font-size: 34px;
    line-height: 1;
    color: var(--green);
  }
  .contact-line {
    position: absolute;
    left: 22px;
    right: 22px;
    bottom: 22px;
    display: flex;
    justify-content: space-between;
    align-items: baseline;
    font-weight: 700;
    font-size: 19px;
    line-height: 1.2;
    white-space: nowrap;
    color: var(--navy);
  }
</style>
</head>
<body>
  <main class="canvas">
    <section class="card card-front" aria-label="Card front">
      <div class="cut-mark">zu</div>
      <div class="domain-suffix">.com.au</div>
    </section>
    <section class="card card-back" aria-label="Card back">
      <div class="cut-mark" aria-hidden="true">zu</div>
      <div class="contact-line">
        <span class="contact-name">Olin Verka</span>
        <span class="contact-email">olin@zu.com.au</span>
        <span class="contact-phone">+61 437 185 923</span>
      </div>
    </section>
  </main>
</body>
</html>
```